New, modern business card for growing audiology practice

We need a new business card for our audiology practice. Our logo and website have recently changed (more modern) and we want our business cards to reflect this change.
We conduct hearing tests, perform earwax removals, and fit & dispense hearing aids to our patients. We are a family owned practice in which the owner is the one who works directly with the patient. I have attached logos in various formats to use, as well as two ideas I found on this website; as well as a scanned copy of our current logo. Good luck!

Industry/Entity Type

Business

Contact Information for Business Card

Company name: Tolvera Hearing Center
Provider name: Peter Wolstenby, Au.D. F/NSB
Phone number: (440) 683-5127
Address: 837 W. Lindell Ave. Marlow Ridge, OH 44187
email: tolverahearing@postvane.com
website: tolverahearing.com

Colors
000000
aaaaaa
dbdbdb
cacaca
9bcb3c
afd23c
cadf82
b1b1b1

Requirements
Must have
• My card must include information in the "details" section. In the attached images, I found a few that I liked and I would like to model after - "brisky bouncin'" and "Sound Method Center".
• Must be horizontal.
• Must include logos provided. I uploaded them in various file formats and various ways.
• Must match logo font, if possible, if not, please get as close as you can.
Nice to have
• I really like the idea of having a color on one side with just the logo and company name and the contact information and provider name on the other side. I also really like the idea of having the main color dominating on the logo/company side with accent of that same color on the contact side of the card.
Should not have
• Must not be vertical.

```html
<!DOCTYPE html>
<html lang="en">
<head>
<meta charset="utf-8">
<title>Tolvera Hearing Center – Business Card</title>
<link href="https://fonts.googleapis.com/css2?family=Roboto:wght@400;500;700&family=Roboto+Condensed:wght@700&display=swap" rel="stylesheet">
<style>
  :root {
    --backdrop: #e9e9e7;
    --card-light: #f3f3f2;
    --card-dark: #1b1c1e;
    --brand-green: #79a83a;
    --ink: #111111;
    --ink-soft: #555555;
    --paper-white: #ffffff;
  }
  * { margin: 0; padding: 0; box-sizing: border-box; }
  html, body {
    width: 1200px; height: 960px; overflow: hidden;
    background: var(--backdrop);
    font-family: "Roboto", Arial, sans-serif;
  }
  .stage { position: relative; width: 1200px; height: 960px; }

  .card {
    position: absolute;
    width: 600px; height: 343px;
    border-radius: 20px;
    overflow: hidden;
  }
  .card-front { left: 314px; top: 113px; background: var(--card-light); }
  .card-back  { left: 312px; top: 472px; background: var(--card-dark); }

  /* front */
  .brand-line {
    position: absolute; left: 54px; top: 56px;
    display: flex; align-items: center; gap: 10px;
  }
  .brand-dot {
    width: 20px; height: 20px; border-radius: 50%;
    background: var(--brand-green);
  }
  .brand-name {
    font-family: "Roboto", Arial, sans-serif;
    font-weight: 400; font-size: 20px; letter-spacing: 0.2px;
    color: var(--ink); text-transform: uppercase;
  }
  .accent-bar {
    position: absolute; left: 0; top: 133px;
    width: 13px; height: 40px; background: var(--brand-green);
  }
  .provider-name {
    position: absolute; left: 50px; top: 130px;
    font-family: "Roboto Condensed", "Arial Narrow", sans-serif;
    font-weight: 700; font-size: 22px; color: var(--brand-green);
    text-transform: uppercase;
  }
  .provider-title {
    position: absolute; left: 50px; top: 157px;
    font-weight: 500; font-size: 15px; color: var(--ink);
    letter-spacing: 0.3px;
  }
  .address {
    position: absolute; left: 50px; top: 199px;
    font-size: 14px; line-height: 18px; color: var(--ink-soft);
  }
  .contact-list {
    position: absolute; left: 50px; top: 246px;
    list-style: none;
    font-size: 14px; line-height: 19px; color: var(--ink-soft);
  }
  .contact-list li { display: flex; align-items: center; gap: 9px; }
  .contact-icon { width: 14px; height: 14px; flex: none; }

  /* back */
  .back-mark {
    position: absolute; left: 0; right: 0; top: 92px;
    display: flex; flex-direction: column; align-items: center; gap: 26px;
  }
  .back-dot {
    width: 110px; height: 110px; border-radius: 50%;
    background: var(--brand-green);
  }
  .back-name {
    font-weight: 500; font-size: 24px; letter-spacing: 1px;
    color: var(--brand-green); text-transform: uppercase;
  }
  .back-web {
    position: absolute; left: 0; right: 0; top: 295px;
    text-align: center;
    font-size: 14px; letter-spacing: 4px; color: var(--paper-white);
  }
</style>
</head>
<body>
<main class="stage">

  <section class="card card-front">
    <div class="brand-line">
      <span class="brand-dot"></span>
      <span class="brand-name">Tolvera Hearing Center</span>
    </div>

    <span class="accent-bar"></span>
    <h1 class="provider-name">Peter Wolstenby</h1>
    <p class="provider-title">AU.D. F/NSB</p>

    <p class="address">837 W. Lindell Ave.<br>Marlow Ridge, OH 44187</p>

    <ul class="contact-list">
      <li>
        <svg class="contact-icon" viewBox="0 0 16 16" aria-hidden="true">
          <path fill="#79a83a" d="M3.6 1.2l2.3 2.6-1.4 1.7c.9 2 2.4 3.6 4.4 4.5l1.7-1.4 2.6 2.3-1.2 2.6C6.6 13.3 2.7 9.4 1 3.6z"/>
        </svg>
        <span>(440) 683-5127</span>
      </li>
      <li>
        <svg class="contact-icon" viewBox="0 0 16 16" aria-hidden="true">
          <rect x="1" y="3.5" width="14" height="9.5" fill="#79a83a"/>
          <path d="M1.5 4l6.5 5 6.5-5" fill="none" stroke="#f3f3f2" stroke-width="1.3"/>
        </svg>
        <span>tolverahearing@postvane.com</span>
      </li>
      <li>
        <svg class="contact-icon" viewBox="0 0 16 16" aria-hidden="true">
          <circle cx="8" cy="8" r="7" fill="#79a83a"/>
          <path d="M5 4.5c1.5.3 1.7 1.6 1 2.5-.7.9.3 1.8 1.2 1.6M10 11.5c-.6-1-.2-2 .9-2.2l1.6.2" fill="none" stroke="#f3f3f2" stroke-width="1.3"/>
        </svg>
        <span>tolverahearing.com</span>
      </li>
    </ul>
  </section>

  <section class="card card-back">
    <div class="back-mark">
      <span class="back-dot"></span>
      <span class="back-name">Tolvera Hearing Center</span>
    </div>
    <p class="back-web">www.tolverahearing.com</p>
  </section>

</main>
</body>
</html>
```